A new presentation to our clients

we are a Real Estate agency, our website is www.lumibrasa.com and it’s time to have a new, fashion and remarcable Business Card. we want to differentiate ourselves from other companies so we want a business card that differentiates us. we want the business card to impact our customers. in the competitive market that we have today, we have to be different and it is this difference that we seek

Target Market(s)

Real Estate Clients

Contact Information for Business Card

We search a totaly diferent card from the usual

Font styles to use
Sans Serif

Colors
e34197

Requirements
Must have
• Logo, adress, phone contact, e-mail, photo, and our website
Nice to have
• We would like to see a modern business card
Should not have
• Houses or building draws

```html
<!DOCTYPE html>
<html lang="pt">
<head>
<meta charset="utf-8">
<title>Lumibrasa – Business Card</title>
<link href="https://fonts.googleapis.com/css2?family=Montserrat:wght@500;600;700&display=swap" rel="stylesheet">
<style>
  :root {
    --brand-pink: #e8286f;
    --text-grey: #8d8d8d;
    --card-white: #ffffff;
    --stage: #2b2b2b;
    --divider: #bdbdbd;
  }
  * { margin: 0; padding: 0; box-sizing: border-box; }
  html, body {
    width: 1200px; height: 791px; overflow: hidden;
    background: var(--stage);
    font-family: "Montserrat", Arial, sans-serif;
  }
  .card {
    position: absolute; left: 158px; top: 142px;
    width: 881px; height: 503px;
    background: var(--card-white);
    border-radius: 28px;
  }
  .brand-name {
    position: absolute; left: 76px; top: 212px;
    width: 370px; text-align: center;
    font-size: 62px; font-weight: 600; line-height: 78px;
    color: var(--brand-pink);
  }
  .divider {
    position: absolute; left: 473px; top: 128px;
    width: 2px; height: 248px;
    background: linear-gradient(to bottom, transparent, var(--divider) 15%, var(--divider) 85%, transparent);
  }
  .person-name {
    position: absolute; left: 513px; top: 132px;
    font-size: 30px; font-weight: 700; line-height: 36px;
    color: var(--brand-pink);
  }
  .person-role {
    position: absolute; left: 513px; top: 166px;
    font-size: 22px; font-weight: 600; line-height: 26px;
    color: var(--text-grey);
  }
  .address {
    position: absolute; left: 513px; top: 203px;
    font-size: 17px; font-weight: 500; line-height: 25px;
    color: var(--text-grey); font-style: normal;
  }
  .contact-list {
    position: absolute; left: 513px; top: 262px;
    list-style: none;
  }
  .contact-list li {
    display: flex; align-items: center; gap: 13px;
    font-size: 17px; font-weight: 500; line-height: 25.6px;
    color: var(--text-grey);
    text-shadow: 0 1px 2px rgba(0,0,0,0.18);
  }
  .contact-list svg { width: 19px; height: 19px; fill: var(--brand-pink); flex: none; }
</style>
</head>
<body>
  <main class="card">
    <div class="brand-name">Lumibrasa</div>
    <div class="divider"></div>
    <h1 class="person-name">RUI MATOS</h1>
    <p class="person-role">CEO/FOUNDER</p>
    <address class="address">Av. das Camélias, 215<br>4410-088, Vila Nova de Gaia</address>
    <ul class="contact-list">
      <li>
        <svg viewBox="0 0 24 24" aria-hidden="true"><path d="M6.6 10.8a15.2 15.2 0 0 0 6.6 6.6l2.2-2.2c.3-.3.7-.4 1-.2 1.1.4 2.3.6 3.6.6.6 0 1 .4 1 1V20c0 .6-.4 1-1 1A17 17 0 0 1 3 4c0-.6.4-1 1-1h3.5c.6 0 1 .4 1 1 0 1.3.2 2.5.6 3.6.1.3 0 .7-.2 1z"/></svg>
        (+351) 220 418 360
      </li>
      <li>
        <svg viewBox="0 0 24 24" aria-hidden="true"><path d="M6 2h12v6H6zM3 9h18a1 1 0 0 1 1 1v7h-4v-3H6v3H2v-7a1 1 0 0 1 1-1zm4 6h10v7H7z"/></svg>
        (+351) 220 418 369
      </li>
      <li>
        <svg viewBox="0 0 24 24" aria-hidden="true"><path d="M2 5h20v14H2zm2 2v.5l8 5.5 8-5.5V7l-8 5.5z"/></svg>
        geral@lumibrasa.com
      </li>
      <li>
        <svg viewBox="0 0 24 24" aria-hidden="true"><circle cx="12" cy="12" r="10"/><path d="M7 8c2 0 3 1 3 3s-2 2-2 4 1 3 1 4M15 4c-1 2 0 3 2 3s2 2 1 4-3 1-3 4" stroke="#fff" stroke-width="1.6" fill="none"/></svg>
        www.lumibrasa.com
      </li>
    </ul>
  </main>
</body>
</html>
```